Frostvale Harborline LLC

we need a business card design

Industry/Entity Type

hvac

Contact Information for Business Card

my logo

Requirements
Must have
• my logo and same colors

```html
<!DOCTYPE html>
<html lang="en">
<head>
<meta charset="utf-8">
<title>Frostvale Harborline LLC – Business Card</title>
<link href="https://fonts.googleapis.com/css2?family=Montserrat:wght@400;500;700&display=swap" rel="stylesheet">
<style>
  :root {
    --backdrop: #cfcfcf;
    --card: #ffffff;
    --brand-blue: #1a56a6;
    --brand-gold: #f2b544;
    --ink: #2a2a2a;
  }
  * { margin: 0; padding: 0; box-sizing: border-box; }
  html, body {
    width: 1200px;
    height: 896px;
    overflow: hidden;
    background: var(--backdrop);
    font-family: "Montserrat", sans-serif;
  }
  .card {
    position: absolute;
    left: 334px;
    width: 528px;
    height: 300px;
    background: var(--card);
    border-radius: 26px;
    box-shadow: 0 14px 22px rgba(0, 0, 0, 0.18);
  }
  .card--front { top: 126px; }
  .card--back { top: 475px; }

  .brand {
    position: absolute;
    left: 0; right: 0; top: 0; bottom: 0;
    display: flex;
    align-items: center;
    justify-content: center;
    gap: 12px;
  }
  .brand__dot {
    width: 22px;
    height: 22px;
    border-radius: 50%;
    background: var(--brand-gold);
  }
  .brand__name {
    font-weight: 700;
    font-size: 24px;
    letter-spacing: 0.5px;
    color: var(--brand-blue);
  }

  .identity {
    position: absolute;
    right: 273px;
    top: 125px;
    text-align: right;
  }
  .identity__name {
    font-weight: 700;
    font-size: 25px;
    color: var(--brand-blue);
    line-height: 1;
    letter-spacing: 0.3px;
  }
  .identity__title {
    font-weight: 500;
    font-size: 14px;
    color: var(--ink);
    margin-top: 8px;
  }
  .divider {
    position: absolute;
    left: 276px;
    top: 123px;
    width: 2px;
    height: 55px;
    background: var(--brand-blue);
  }
  .contacts {
    position: absolute;
    left: 303px;
    top: 119px;
    list-style: none;
  }
  .contacts li {
    display: flex;
    align-items: center;
    gap: 6px;
    font-size: 14.5px;
    color: var(--ink);
    height: 21px;
  }
  .contacts svg { width: 12px; height: 12px; fill: var(--brand-blue); }
  .address {
    position: absolute;
    left: 0; right: 0;
    bottom: 20px;
    text-align: center;
    font-size: 14px;
    color: var(--ink);
  }
</style>
</head>
<body>
  <section class="card card--front">
    <div class="brand">
      <span class="brand__dot"></span>
      <span class="brand__name">FROSTVALE HARBORLINE LLC</span>
    </div>
  </section>

  <section class="card card--back">
    <div class="identity">
      <div class="identity__name">MARCUS HALE</div>
      <div class="identity__title">Managing Director</div>
    </div>
    <div class="divider"></div>
    <ul class="contacts">
      <li>
        <svg viewBox="0 0 12 12"><path d="M1 4.5C1 3 3 2 6 2s5 1 5 2.5L9.5 5.5 8 4.5V3.8H4v.7L2.5 5.5z M3 6h6l1.5 4h-9z"/></svg>
        123 456 789
      </li>
      <li>
        <svg viewBox="0 0 12 12"><path d="M1 3h10v1L6 7 1 4z M1 5.2l5 3 5-3V10H1z"/></svg>
        info@yourgmail.com
      </li>
      <li>
        <svg viewBox="0 0 12 12"><circle cx="6" cy="6" r="5"/><path d="M4 3.5l2 1-1 2 1.5 2-2 .5z M7.5 2.8l1.5 1.2-.6 1.8z" fill="#fff"/></svg>
        www.yourwebsite.com
      </li>
    </ul>
    <div class="address">Your address, City State, Zip 1234</div>
  </section>
</body>
</html>
```